Print materials for 3-star hotel

We are changing up our print materials (notepads, letterheads, key card jackets, small flyer for the room rates) We are a 3 star business hotel in the Philippines and have mainly used grey tones and clean, simple lines. See attached photos for logo and hotel interior photos.

Target Market(s)

Business

Contact Information for Business Card

Corvale Terrace Hotel
Lindwell Banca Avenue corner Tolenta St Cebu City 6000 Philippines
Tel: +63 32 481 7302
Mobile: +63 917 648 2095
www.corvaleterracehotel.example

Font styles to use
Serif
Sans Serif

Requirements
Must have
• Simple
• Readable font and font size
Nice to have
• Neutral colors, grey and taupes
Should not have
• No purples and bright blues

```html
<!DOCTYPE html>
<html lang="en">
<head>
<meta charset="utf-8">
<title>Corvale Terrace Hotel – Business Card</title>
<link rel="stylesheet" href="https://fonts.googleapis.com/css2?family=Cinzel:wght@400;500&family=Roboto:wght@400;500&display=swap">
<style>
  :root {
    --backdrop: #3b3b3d;
    --card: #1d1d1e;
    --taupe: #c9b99d;
    --edge: #8a7d68;
  }
  html, body {
    margin: 0;
    padding: 0;
    width: 1200px;
    height: 900px;
    overflow: hidden;
    background: var(--backdrop);
  }
  .canvas {
    position: relative;
    width: 1200px;
    height: 900px;
  }
  .card {
    position: absolute;
    left: 250px;
    width: 700px;
    height: 400px;
    background: var(--card);
    box-shadow: 0 0 0 1px var(--edge), 0 14px 30px rgba(0,0,0,.45);
    color: var(--taupe);
    box-sizing: border-box;
  }
  .card--front { top: 35px; }
  .card--back { top: 465px; }

  /* front */
  .brand {
    position: absolute;
    inset: 0;
    display: flex;
    flex-direction: column;
    align-items: center;
    justify-content: center;
  }
  .brand__square {
    width: 58px;
    height: 58px;
    background: var(--taupe);
    margin-bottom: 22px;
  }
  .brand__name {
    font-family: "Cinzel", serif;
    font-weight: 400;
    font-size: 27px;
    letter-spacing: 5px;
    margin: 0;
    line-height: 1;
  }
  .brand__sub {
    font-family: "Cinzel", serif;
    font-weight: 400;
    font-size: 15px;
    letter-spacing: 6px;
    margin-top: 6px;
  }

  /* back */
  .contact {
    position: absolute;
    left: 80px;
    top: 70px;
    font-family: "Roboto", sans-serif;
    font-size: 16px;
    line-height: 1.3;
  }
  .contact__name {
    font-family: "Cinzel", serif;
    font-size: 22px;
    font-weight: 500;
    letter-spacing: 1px;
    margin: 0;
  }
  .contact__role {
    font-weight: 500;
    font-size: 14px;
    margin: 0;
  }
  .contact__rule {
    width: 36px;
    height: 2px;
    background: var(--taupe);
    margin: 14px 0;
  }
  .contact p { margin: 0; }
  .contact__lines { margin-top: 22px; }
  .contact__lines p { font-size: 15px; }

  .mark-block {
    position: absolute;
    right: 90px;
    top: 85px;
    width: 230px;
    height: 230px;
    background: var(--taupe);
  }
</style>
</head>
<body>
<div class="canvas">
  <section class="card card--front">
    <div class="brand">
      <div class="brand__square"></div>
      <h1 class="brand__name">Corvale Terrace</h1>
      <div class="brand__sub">Hotel</div>
    </div>
  </section>

  <section class="card card--back">
    <div class="contact">
      <h2 class="contact__name">RAFAEL MONTAÑO</h2>
      <p class="contact__role">CEO/Founder</p>
      <div class="contact__rule"></div>
      <p>Lindwell Banca Avenue</p>
      <p>Cebu City 6000 Philippines</p>
      <div class="contact__rule"></div>
      <div class="contact__lines">
        <p>+63 917 648 2095</p>
        <p>rafael@corvaleterrace.example</p>
        <p>www.corvaleterracehotel.example</p>
      </div>
    </div>
    <div class="mark-block"></div>
  </section>
</div>
</body>
</html>
```